Tessel - Web Design Project

We are seeking to have our website redesigned. Our current webpage is rather dated looking www.tessel-momentum.example We will be utilizing similar content to explain our services as what is in the website now. We do not see it at a retail portal but rather a website for those inquiring about our services as a reference check so to speak.

We wish to have a look that is considered clean, fresh, contemporary and contains a business savvy vibe.

We prefer isolated white background and also wish to retain the integrity of our Logo and colour scheme.

We are looking for something that doesnt look like it was designed at home on sitenook. We are hoping to find something that looks like it would reside on a tablet.

Hello designers!

We apologize for our tardiness as we have been quite preoccupied. We will be extending our invites to the end of January!

Hello All,

Please review our offer once again for updated requirements.  We are hoping to accept a design by months end.

Tessel

Target Market(s)

Business to business clients and Large manufacturers

Industry/Entity Type

Retail

Requirements
Must have
• Existing Logo

There must be an area dedicated to an intro video that will be incorporated on our landing page.

We require design of the other pages as well not only the landing page.

```html
<!DOCTYPE html>
<html lang="en">
<head>
<meta charset="utf-8">
<title>Tessel Performance Group – Website Design</title>
<link rel="stylesheet" href="https://fonts.googleapis.com/css2?family=Open+Sans:wght@400;600;700&family=Arimo:wght@400;700&display=swap">
<style>
:root{
  --red:#b3121b;
  --red-bright:#d8232a;
  --ink:#2d2d2d;
  --grey:#777;
  --light:#f2f2f2;
  --rule:#dcdcdc;
  --nav:#262626;
  --footer:#141414;
  --blue:#2a7fc8;
  --orange:#f3a11c;
}
*{box-sizing:border-box;margin:0;padding:0}
html,body{width:1200px;height:900px;overflow:hidden;background:#fff}
body{position:relative;font-family:"Arimo",Arial,sans-serif;color:var(--ink)}
.panel{position:absolute;background:linear-gradient(90deg,#c9ccc4,#e4e6df 50%,#c9ccc4)}
.page{position:absolute;background:#fff;overflow:hidden}
.abs{position:absolute}
h2,h3,.ttl{font-family:"Open Sans",Arial,sans-serif;font-weight:400}
.red{color:var(--red)}

/* ---------- landing page ---------- */
.home{left:7px;top:88px;width:600px;height:644px}
.home .page{left:36px;top:0;width:534px;height:644px}
.logo{left:14px;top:16px;display:flex;align-items:center;gap:5px}
.logo .mark{width:10px;height:10px;border-radius:50%;background:var(--red-bright)}
.logo .name{font-family:"Open Sans",sans-serif;font-weight:600;font-size:25px;line-height:28px;color:#555;letter-spacing:-.5px}
.tagline{left:6px;top:53px;font-family:"Open Sans",sans-serif;font-size:9px;font-weight:600;color:#555}
.social{display:flex;gap:5px}
.social i{width:16px;height:16px;border-radius:50%;background:#333;display:block}
.home .social{left:371px;top:20px}
.signin{left:371px;top:47px;font-size:6px;color:#777}
.nav{left:0;top:70px;width:534px;height:25px;background:var(--nav);display:flex}
.nav a{color:#fff;font-size:6px;text-decoration:none;display:flex;align-items:center;gap:4px;padding:0 9px;border-right:1px solid #3a3a3a;white-space:nowrap}
.nav a b{width:6px;height:6px;background:#ddd;display:block;border-radius:1px}
.nav a.active{background:var(--red-bright);width:54px;justify-content:center}

/* intro video hero */
.intro-video{left:0;top:95px;width:534px;height:226px;background:linear-gradient(120deg,#d9dde0 0%,#b8c2cc 35%,#8c97a3 60%,#c8ccd0 100%)}
.play-button{left:106px;top:180px;width:46px;height:46px;border-radius:50%;background:rgba(20,20,20,.55);border:2px solid #fff;display:flex;align-items:center;justify-content:center}
.hero-card{left:242px;top:190px;width:242px;height:108px;border-radius:14px;background:rgba(170,20,25,.88);border:1px solid #e8c8c8;text-align:center;color:#fff}
.hero-card h3{color:var(--orange);font-size:13px;margin-top:36px}
.hero-card p{font-size:6px;line-height:8px;margin:8px 18px 0}
.strip{left:0;top:321px;width:534px;height:82px;background:linear-gradient(#64b8ee,#4b9fd8)}
.thumb{top:10px;width:91px;height:62px;border:2px solid #fff;background:linear-gradient(135deg,#d8dee4,#9aa6b2)}
.arrow{top:32px;width:14px;height:20px;background:#fff;display:flex;align-items:center;justify-content:center}
.welcome{left:0;top:430px;width:534px;text-align:center;font-size:14.5px;color:#333}
.intro{left:16px;top:458px;width:496px;font-size:5.6px;line-height:8px;color:#888}
.features{left:0;top:526px;width:534px;display:flex}
.feature{width:133.5px;text-align:center}
.feature svg{display:block;margin:0 auto 14px}
.feature h4{font-family:"Open Sans",sans-serif;font-weight:600;font-size:10.5px;line-height:14px;color:#222}
.feature p{font-size:5.6px;line-height:8px;color:#888;margin:6px 14px 0}

/* ---------- performance solutions page ---------- */
.inner{left:611px;top:93px;width:589px;height:639px;background:linear-gradient(90deg,#8f968f,#c0c4bd 50%,#8f968f)}
.inner .page{left:36px;top:0;width:534px;height:639px}
.section-title{left:0;width:534px;display:flex;align-items:center;gap:8px;font-size:11px;color:#333}
.section-title::before,.section-title::after{content:"";flex:1;height:1px;background:var(--rule)}
.card{top:23px;width:164px;height:224px;border:1px dashed #bbb;border-top:none;background:#fff;box-shadow:0 3px 3px rgba(0,0,0,.15);text-align:center}
.card .bar{height:7px;background:#666}
.card .photo{margin:8px auto 0;width:155px;height:97px}
.card h5{font-family:"Open Sans",sans-serif;font-weight:600;font-size:9.5px;color:#333;margin-top:22px;display:flex;align-items:center;justify-content:center;gap:5px;line-height:13px}
.card p{font-size:6px;line-height:8px;color:#777;margin:5px 12px 0}
.card .btn{display:inline-block;margin-top:8px;background:#1e1e1e;color:#fff;font-size:6.5px;padding:5px 10px;border-radius:2px}
.clients{left:0;top:314px;width:534px;display:flex;justify-content:space-around;align-items:center}
.client{display:flex;align-items:center;gap:4px;font-family:"Open Sans",sans-serif;font-weight:700;font-size:12px;color:#555}
.client i{width:13px;height:13px;background:#c9c9c9;display:block}
.newsletter{left:0;top:377px;width:534px;height:50px;background:var(--light)}
.quote{left:10px;top:10px;width:250px;font-size:6px;line-height:8px;color:#555}
.envelope{left:276px;top:14px;width:26px;height:24px;background:#e9c93b;border:1px solid #c9a624}
.search{left:371px;top:19px;width:114px;height:15px;background:#fff;border:1px solid #ccc;font-size:6px;color:#aaa;padding:4px 3px}
.submit{left:485px;top:19px;width:37px;height:15px;background:var(--blue);color:#fff;font-size:7px;font-weight:700;text-align:center;line-height:15px}
.footer{left:0;top:429px;width:534px;height:193px;background:var(--footer);border-top:2px solid var(--blue);color:#888}
.footer h6{font-family:"Open Sans",sans-serif;font-weight:600;font-size:10.5px;color:#fff}
.footer h6 span{color:var(--red-bright)}
.fcol{top:18px}
.footer .small{font-size:5.8px;line-height:8px;color:#777}
.tweet{display:flex;gap:10px;margin-top:12px;width:150px}
.tweet i{width:18px;height:18px;background:#666;flex:none}
.gallery{display:grid;grid-template-columns:repeat(4,34px);gap:5px;margin-top:14px}
.gallery i{height:32px;border:2px solid var(--red);background:linear-gradient(135deg,#b9c6d2,#6d7e90);display:block}
</style>
</head>
<body>

<section class="panel home" aria-label="Landing page">
  <div class="page">
    <div class="abs logo"><span class="mark"></span><span class="name">Tessel</span></div>
    <div class="abs tagline">Tessel <span class="red">Performance</span> Group</div>
    <div class="abs social" aria-label="Social links"><i></i><i></i><i></i><i></i><i></i></div>
    <div class="abs signin">Sign In | Français</div>

    <nav class="abs nav">
      <a class="active" href="#"><b></b>Home</a>
      <a href="#"><b></b>Who We Are</a>
      <a href="#"><b></b>Cross The Tessel</a>
      <a href="#"><b></b>Performance Solutions</a>
      <a href="#"><b></b>Sustain Solutions</a>
      <a href="#"><b></b>Join Us</a>
      <a href="#"><b></b>Contact Us</a>
    </nav>

    <div class="abs intro-video" role="img" aria-label="Intro video area, poster photo of a smiling business team in a bright office"></div>
    <div class="abs play-button" aria-label="Play intro video">
      <svg width="16" height="18" viewBox="0 0 16 18"><path d="M2 1l13 8-13 8z" fill="#fff"/></svg>
    </div>
    <div class="abs hero-card">
      <h3>Executive Coaching</h3>
      <p>Gain the deep strategic capabilities of a top multinational consultancy and the cost advantages of a best-in-class technology company.</p>
    </div>

    <div class="abs strip">
      <div class="abs arrow" style="left:5px"><svg width="6" height="8"><path d="M5 0L1 4l4 4" fill="none" stroke="#333" stroke-width="1.4"/></svg></div>
      <div class="abs thumb" style="left:27px" role="img" aria-label="Business team photo"></div>
      <div class="abs thumb" style="left:126px" role="img" aria-label="Team standing together photo"></div>
      <div class="abs thumb" style="left:225px" role="img" aria-label="Group of colleagues photo"></div>
      <div class="abs thumb" style="left:323px" role="img" aria-label="Diverse team photo"></div>
      <div class="abs thumb" style="left:421px" role="img" aria-label="Office colleagues photo"></div>
      <div class="abs arrow" style="left:515px"><svg width="6" height="8"><path d="M1 0l4 4-4 4" fill="none" stroke="#333" stroke-width="1.4"/></svg></div>
    </div>

    <h2 class="abs welcome">Welcome to <span class="red">Tessel Performance Group</span></h2>
    <p class="abs intro">Tessel Performance Group Inc. is the leading provider of profit generating and people development solutions. With the hands-on experience of best practices, the state-of-the-art technology and in-depth information we help companies increase their efficiencies and profits. Frank, honest, committed, valuable and rewarding are words that customers use to describe the quality services provided by Tessel Performance Group.<br><br>Learn more about us, or find the right solutions for your specific business.We will be delighted to help you achieve better business results.</p>

    <div class="abs features">
      <div class="feature">
        <svg width="28" height="28" viewBox="0 0 28 28"><circle cx="14" cy="14" r="12" fill="none" stroke="#222" stroke-width="2"/><path d="M7 9c3 0 4 2 3 4s1 4 3 4-1 5 1 6M17 5c-1 3 2 4 4 3s3 3 2 5" fill="none" stroke="#222" stroke-width="2"/></svg>
        <h4>Talent <span class="red">Management</span></h4>
        <p>This template has a responsive design, which means you can resize the browser to any size, and the layout will change. Try it out on your phone or tablet!</p>
      </div>
      <div class="feature">
        <svg width="28" height="28" viewBox="0 0 28 28"><rect x="2" y="6" width="18" height="13" fill="none" stroke="#222" stroke-width="2"/><path d="M7 23h8" stroke="#222" stroke-width="2"/><rect x="18" y="11" width="8" height="12" fill="#fff" stroke="#222" stroke-width="2"/></svg>
        <h4>Creating <span class="red">Sales<br>Culture</span></h4>
        <p>This Template is built with <span style="color:#d9a08c">StyleKit</span>, which allows you to change the site using a few variables(like colors and font-size).</p>
      </div>
      <div class="feature">
        <svg width="28" height="28" viewBox="0 0 28 28"><circle cx="10" cy="10" r="6" fill="none" stroke="#222" stroke-width="4" stroke-dasharray="3 2"/><circle cx="10" cy="10" r="2" fill="#222"/><circle cx="21" cy="20" r="4" fill="none" stroke="#222" stroke-width="3" stroke-dasharray="2 1.5"/></svg>
        <h4>Creating <span class="red">Customer<br>Loyalty</span></h4>
        <p>This Template is built with <span style="color:#d9a08c">StyleKit</span>, which allows you to change the site using a few variables(like colors and font-size).</p>
      </div>
      <div class="feature">
        <svg width="28" height="28" viewBox="0 0 28 28"><path d="M14 22C10 17 11 10 14 6c3 4 4 11 0 16zM13 22C8 21 4 17 3 12c5 0 9 4 10 10zM15 22c5-1 9-5 10-10-5 0-9 4-10 10z" fill="#222"/></svg>
        <h4>Product <span class="red">Launches</span></h4>
        <p>We love all our Marketstall customers, and with a premium template comes premium support.</p>
      </div>
    </div>
  </div>
</section>

<section class="panel inner" aria-label="Performance Solutions page">
  <div class="page">
    <h3 class="abs section-title" style="top:3px">Our <span class="red">Performance Solutions</span></h3>

    <article class="abs card" style="left:0">
      <div class="bar"></div>
      <div class="photo" role="img" aria-label="Photo of a team meeting around a table" style="background:linear-gradient(135deg,#e6e6e6,#8d8f94)"></div>
      <h5><svg width="14" height="14"><circle cx="5" cy="6" r="3.5" fill="none" stroke="#777"/><circle cx="10" cy="9" r="3" fill="none" stroke="#777"/></svg>Business Diagnostics</h5>
      <p>Lorem hac habitasse platea dictumst. Aliquam in est leo. Aliquam ut urna pulvinar ipsum ultricies fringilla et sed magna. Duis faucibus lorem at leo.</p>
      <span class="btn">know more...</span>
    </article>
    <article class="abs card" style="left:185px">
      <div class="bar"></div>
      <div class="photo" role="img" aria-label="Photo of a presenter at a flip chart" style="background:linear-gradient(135deg,#f4f4f4,#b0b4ba)"></div>
      <h5><svg width="14" height="14"><rect x="1" y="2" width="11" height="11" rx="2" fill="none" stroke="#777"/><path d="M5 9l7-8" stroke="#777"/></svg>Executive Coaching</h5>
      <p>Lorem hac habitasse platea dictumst. Aliquam in est leo. Aliquam ut urna pulvinar ipsum ultricies fringilla et sed magna. Duis faucibus lorem at eros.</p>
      <span class="btn">know more...</span>
    </article>
    <article class="abs card" style="left:370px">
      <div class="bar"></div>
      <div class="photo" role="img" aria-label="Photo of managers seated in a training session" style="background:linear-gradient(135deg,#b24a2c,#e0a07a 60%,#6e6e72)"></div>
      <h5><svg width="14" height="14"><circle cx="7" cy="4" r="3" fill="none" stroke="#777"/><path d="M2 13c0-4 10-4 10 0" fill="none" stroke="#777"/></svg>Management<br>Development</h5>
      <p>Lorem hac habitasse platea dictumst. Aliquam in est leo. Aliquam ut urna pulvinar ipsum ultricies fringilla et sed magna. Duis faucibus</p>
      <span class="btn">know more...</span>
    </article>

    <h3 class="abs section-title" style="top:283px">Our <span class="red">Clients &amp; Partners List</span></h3>
    <div class="abs clients">
      <span class="client"><i></i>Norland</span>
      <span class="client"><i></i>Cloudrise Software</span>
      <span class="client"><i></i>Meridian Wire</span>
      <span class="client"><i></i>Orbitalk</span>
    </div>

    <h3 class="abs section-title" style="top:356px">Register here <span class="red">For Tessel Performance Group Newsletters</span></h3>
    <div class="abs newsletter">
      <p class="abs quote">"There are managers so preoccupied with their e-mail messages that they never look up from their screens to see what's happening in the nondigital world."<br>– <b>Harlan Vossberg</b></p>
      <div class="abs envelope"></div>
      <div class="abs search">Site Search</div>
      <div class="abs submit">submit</div>
    </div>

    <footer class="abs footer">
      <div class="abs fcol" style="left:16px">
        <h6>Follow <span>Us on</span></h6>
        <p class="small" style="margin-top:18px;font-style:italic">Visit Our Social Network</p>
        <div class="social" style="margin-top:6px"><i style="background:#444"></i><i style="background:#444"></i><i style="background:#444"></i><i style="background:#444"></i><i style="background:#444"></i></div>
        <div class="logo" style="position:static;margin-top:10px"><span class="mark"></span><span class="name" style="font-size:20px;color:#666">Tessel</span></div>
        <p class="small" style="margin-top:14px">© Copyright 2011. All rights reserved.<br>Tessel Performance Group,88 Harbour Lane,<br>Kingsford,ON K0K 1A0 , Canada . T: +1 555 010 2040<br>Email:<span style="color:#ccc">info@tessel-momentum.example</span> | <span style="color:#ccc">Site Map</span></p>
      </div>
      <div class="abs fcol" style="left:189px">
        <h6>Chatter <span>Widget</span></h6>
        <div class="tweet" style="margin-top:16px"><i></i><p class="small">@Tessel Performance Group Inc. is the leading provider of profit generating and people development solutions.</p></div>
        <div class="tweet"><i></i><p class="small">@Tessel Performance Group Inc. is the leading provider of profit generating and people development solutions.</p></div>
      </div>
      <div class="abs fcol" style="left:363px">
        <h6>Snapline <span>Widget</span></h6>
        <div class="gallery" role="img" aria-label="Gallery of small business photos">
          <i></i><i></i><i></i><i></i><i></i><i></i><i></i><i></i><i></i>
        </div>
      </div>
    </footer>
  </div>
</section>

</body>
</html>
```